PostCard Design Project

I am making a mailing postcard
I am having the mailing printed using 4 color foil on certain parts.
I am looking for a design that maximizes the foil process where certain parts are done in foil to grab the customers attention (example: if there is a car on the postcard the headlights would be done in foil) .
I am targeting some industries, (auto, real estate, medical, beauty) I would like the post card to have examples of postcard ideas for 2 or 3 of these industries.
specs:
the postcard should be atleast 6.5x9 up to 8.5x11, I don't want to restrict the space for the creative as I don't want everything to look like a huge mess. both sides will be used.
the piece is a direct mail piece so it has to meet requirements of https://www.mailvantor.com/business/pdf/quick-reference-guide.pdf
text will be
"business with no limits, meet mailing with no addresses, gain new customers through "Open Porch Route Drop" reach new customers at their home without needing their address. "
I also want some current print specials I am running included.
-double your order FREE (order 500 business cards and get 1000)
-250 100lb gloss stock brochures 99.00
-business packages (cards, envelopes and letterhead) 299
-1000 flyers 140.40
-5000 postcards 179.99
A list of services
banners
booklets
brochures
business cards
calendars
catalogs
CD/DVD packages
envelopes
event tickets
flyers
hangtags
postcards
posters
presentation folders
rack cards
labels
table tents
window cling and decal
"order 24/7 orders@inkwillow.com" must be included
my logo is InkWillow will be supplied later
ive received some great designs. however Im looking for something a little more modern like some zorvel would put out. if the amount of words is too much please feel free to edit. also an idea i had for the list of services i offer is to have it transparent yet readable as the background of the postcard some small some big but covering the entire backgroud. you can then design on top of that with other thing. just an early morning thought
Reason: I have uploaded a sketch of my idea, please take time to look at it for an accurate depiction of what im looking for. feel free to add elements that make it pop off the page
Reason: We are getting close i will be providing feed back today

```html
<!DOCTYPE html>
<html lang="en">
<head>
<meta charset="utf-8">
<title>InkWillow Mailing Postcard</title>
<link rel="stylesheet" href="https://fonts.googleapis.com/css2?family=Arimo:wght@700&family=Source+Sans+3:wght@400&display=swap">
<style>
  :root {
    --stage: #e9e6e1;
    --ink-black: #0f0f10;
    --navy-dark: #15202d;
    --navy-light: #2b4258;
    --lime: #b5d334;
    --cyan: #1ea6d6;
    --white: #ffffff;
    --text-dark: #1b1b1b;
    --photo-light: #f4f5f6;
    --photo-mid: #c9ccd0;
  }
  html, body {
    margin: 0;
    width: 1200px;
    height: 900px;
    overflow: hidden;
    background: var(--stage);
  }
  .postcard {
    position: relative;
    width: 1200px;
    height: 900px;
  }
  .postcard-shapes {
    position: absolute;
    inset: 0;
  }
  .headline {
    position: absolute;
    left: 573px;
    top: 126px;
    margin: 0;
    font-family: "Arimo", Arial, sans-serif;
    font-weight: 700;
    font-size: 23px;
    line-height: 38px;
    color: var(--white);
    text-transform: uppercase;
    white-space: nowrap;
  }
  .specials {
    position: absolute;
    left: 560px;
    top: 411px;
    margin: 0;
    padding: 0;
    list-style: none;
    font-family: "Source Sans 3", "Myriad Pro", sans-serif;
    font-size: 26.5px;
    line-height: 33px;
    color: var(--white);
    white-space: nowrap;
  }
  .specials li {
    position: relative;
    padding-left: 27px;
  }
  .specials li::before {
    content: "";
    position: absolute;
    left: 2px;
    top: 12px;
    width: 12px;
    height: 12px;
    border-radius: 50%;
    background: var(--lime);
  }
  .contact {
    position: absolute;
    left: 150px;
    top: 768px;
    width: 455px;
    text-align: center;
    font-family: "Source Sans 3", "Myriad Pro", sans-serif;
    font-size: 23px;
    line-height: 33px;
    color: var(--text-dark);
  }
  .contact p { margin: 0; }
  .brand-name {
    position: absolute;
    left: 640px;
    top: 752px;
    width: 390px;
    text-align: center;
    margin: 0;
    font-family: "Arimo", Arial, sans-serif;
    font-weight: 700;
    font-size: 35px;
    color: var(--lime);
  }
</style>
</head>
<body>
<main class="postcard">
  <svg class="postcard-shapes" width="1200" height="900" viewBox="0 0 1200 900">
    <defs>
      <linearGradient id="navyPanel" x1="0" y1="0" x2="1" y2="0">
        <stop offset="0" stop-color="var(--navy-light)"/>
        <stop offset="1" stop-color="var(--navy-dark)"/>
      </linearGradient>
      <linearGradient id="photoTone" x1="0" y1="0" x2="1" y2="1">
        <stop offset="0" stop-color="var(--photo-light)"/>
        <stop offset="1" stop-color="var(--photo-mid)"/>
      </linearGradient>
    </defs>

    <rect class="card-base" x="88" y="62" width="1020" height="796" fill="var(--ink-black)"/>

    <path class="stripe-lime" d="M548 62 C440 260 448 560 520 705 L548 705 C478 560 470 260 585 62 Z" fill="var(--lime)"/>
    <path class="stripe-cyan" d="M566 62 C460 260 466 560 534 705 L548 705 C478 560 470 260 585 62 Z" fill="var(--cyan)"/>
    <path class="stripe-gap" d="M578 62 C472 260 476 560 542 705 L548 705 C482 560 476 260 585 62 Z" fill="var(--ink-black)"/>
    <path class="navy-panel" d="M586 62 L1108 62 L1108 705 L550 705 C486 560 480 260 586 62 Z" fill="url(#navyPanel)"/>

    <polygon class="photo-frame" points="113,90 437,90 437,285 113,310" fill="var(--cyan)"/>
    <polygon class="photo-folded-brochures" role="img" aria-label="Photo of folded blue business brochures" points="121,98 429,98 429,278 121,301" fill="url(#photoTone)"/>

    <polygon class="photo-frame" points="113,350 437,290 437,517 113,517" fill="var(--cyan)"/>
    <polygon class="photo-flyer-fan" role="img" aria-label="Photo of a fan of colourful flyers" points="121,357 429,299 429,509 121,509" fill="url(#photoTone)"/>

    <polygon class="photo-frame" points="113,546 437,546 437,700 113,772" fill="var(--cyan)"/>
    <polygon class="photo-card-fan" role="img" aria-label="Photo of a fan of printed business cards" points="121,554 429,554 429,694 121,763" fill="url(#photoTone)"/>

    <rect class="brand-box-frame" x="520" y="702" width="588" height="156" fill="var(--cyan)"/>
    <rect class="brand-box" x="528" y="712" width="572" height="138" fill="var(--ink-black)"/>
    <polygon class="contact-band-frame" points="88,786 548,702 628,858 88,858" fill="var(--cyan)"/>
    <polygon class="contact-band" points="96,795 543,714 617,850 96,850" fill="var(--lime)"/>
  </svg>

  <p class="headline">“ Business with no limits,<br>meet mailing with no addresses,<br>gain new customers through<br>"Open Porch Route Drop"<br>reach new customers at their home<br>without needing their address. ”</p>

  <ul class="specials">
    <li>Double your order FREE<br>(order 500 business cards and get 1000)</li>
    <li>250 100lb gloss stock brochures 99.00</li>
    <li>Business packages<br>(cards, envelopes and letterhead) 299</li>
    <li>1000 flyers 140.40</li>
    <li>5000 postcards 179.99</li>
  </ul>

  <div class="contact">
    <p>Contact Us :</p>
    <p>order 24/7 orders@inkwillow.com</p>
  </div>

  <p class="brand-name">YOUR LOGO HERE</p>
</main>
</body>
</html>
```